Harborview Estates Business Card for Apartment Buildings

Create business cards for resident managers who run apartment buildings. The audience is the public who are searching for apartment rentals, and current residents who live at the apartment building. Key design element will be incorporating the company logo, however, the logo cannot dominate. The building name and manager name are more important than the logo. Current business card design leaves little room for copy, so we may need to reduce the size on the current card to allow for more space for copy.

Target Market(s)

Adults 18-65 years of age, who are looking for an apartment rental, plus current residents who live at our apartment buildings.

Industry/Entity Type

Property Management

Contact Information for Business Card

A major design element will be use of the company logo. Important property and manager contact information must be part of the design. The size of the logo will need to be reduced to make room for building and manager contact copy.

Font styles to use
Sans Serif

Colors
3176b5
000000
959595
ffffff

Requirements
Must have
• 1) Incorporate the company logo.
• 2) Use the company colors (dark blue, black/grey, over white).
• 3) FEATURE THE BUILDING NAME
• 4) FEATURE THE MANAGER NAME
• 5) The company name is less important than BUILDING and MANAGER
• 6) Manager contact information
• **SEE ATTACHED CREATIVE BRIEF**
Nice to have
• 1) Back of card logo watermark
• 2) Ability to write notes on back of carfd
Should not have
• Avoid letting the company logo dominate the card, the building name and manager are more important than the company logo.

```html
<!DOCTYPE html>
<html lang="en">
<head>
<meta charset="utf-8">
<title>Harborview Estates – Resident Manager Card</title>
<link rel="stylesheet" href="https://fonts.googleapis.com/css2?family=Roboto:wght@400;500;700&family=Roboto+Condensed:wght@500;700&display=swap">
<style>
  :root {
    --brand-blue: #1a6fb3;
    --back-blue: #1769a8;
    --ink-grey: #4a4a4a;
    --rule-grey: #4d4d4f;
    --paper: #f7f7f7;
    --white: #ffffff;
    --stage: #262626;
  }
  * { margin: 0; padding: 0; box-sizing: border-box; }
  html, body { width: 1200px; height: 960px; overflow: hidden; }
  body {
    background: var(--stage);
    position: relative;
    font-family: "Roboto", Arial, sans-serif;
  }
  .card {
    position: absolute;
    left: 320px;
    width: 600px;
    height: 342px;
  }
  .card-back {
    top: 108px;
    background: var(--back-blue);
  }
  .card-front {
    top: 492px;
    background: var(--paper);
    overflow: hidden;
  }
  .company-name {
    position: absolute;
    right: 30px;
    top: 72px;
    font-family: "Roboto Condensed", Arial, sans-serif;
    font-weight: 700;
    font-size: 26px;
    color: var(--brand-blue);
    letter-spacing: 0.5px;
  }
  .name-band {
    position: absolute;
    left: 0;
    top: 163px;
    width: 262px;
    height: 57px;
  }
  .name-rule {
    position: absolute;
    left: 255px;
    top: 163px;
    width: 345px;
    height: 4px;
    background: var(--rule-grey);
  }
  .manager {
    position: absolute;
    left: 35px;
    top: 167px;
    color: var(--white);
  }
  .manager-name {
    font-family: "Roboto Condensed", Arial, sans-serif;
    font-weight: 700;
    font-size: 23px;
    line-height: 26px;
  }
  .manager-title {
    font-size: 15px;
    font-weight: 500;
    line-height: 20px;
  }
  .property {
    position: absolute;
    left: 32px;
    top: 266px;
    font-size: 14.5px;
    line-height: 19px;
    color: var(--ink-grey);
  }
  .property-name {
    color: var(--brand-blue);
    font-weight: 700;
    font-size: 15px;
  }
  .contacts {
    position: absolute;
    right: 28px;
    top: 226px;
    list-style: none;
    font-size: 14.5px;
    line-height: 19.5px;
    color: var(--ink-grey);
    text-align: right;
  }
  .contacts li {
    display: flex;
    justify-content: flex-end;
    align-items: center;
    gap: 8px;
  }
  .contacts svg {
    width: 13px;
    height: 13px;
    fill: var(--brand-blue);
    flex: none;
  }
</style>
</head>
<body>
  <section class="card card-back" aria-label="Card back"></section>

  <section class="card card-front" aria-label="Card front">
    <div class="company-name">Harborview Estates</div>

    <svg class="name-band" viewBox="0 0 262 57" aria-hidden="true">
      <polygon points="0,0 262,0 212,57 0,57" fill="var(--brand-blue)"/>
    </svg>
    <div class="name-rule"></div>
    <div class="manager">
      <div class="manager-name">Marisol Delgado</div>
      <div class="manager-title">Resident Manager</div>
    </div>

    <address class="property" style="font-style:normal">
      <div class="property-name">Bayside Gardens Apartments</div>
      <div>2418 Juniper Street</div>
      <div>Port Alder, CA 94012</div>
    </address>

    <ul class="contacts">
      <li>555-214-3080
        <svg viewBox="0 0 16 16" aria-label="Office phone"><path d="M3.5 1l2.6 3-1.4 1.9c.9 2 2.5 3.6 4.5 4.5l1.9-1.4 3 2.6-1.6 2.4C7 14 2 9 1.1 2.6z"/></svg>
      </li>
      <li>555-214-7721
        <svg viewBox="0 0 16 16" aria-label="Mobile"><path d="M4 0h8v16H4zM5.5 2v10h5V2zM7 13.2h2v1.3H7z" fill-rule="evenodd"/></svg>
      </li>
      <li>555-214-9045
        <svg viewBox="0 0 16 16" aria-label="Fax"><path d="M4 1h8v4H4zM1 6h14v7h-3v2H4v-2H1zM5 11v2.5h6V11z" fill-rule="evenodd"/></svg>
      </li>
      <li>marisol@harborviewest.com
        <svg viewBox="0 0 16 16" aria-label="Email"><path d="M1 3h14v10H1zM2.5 4.5L8 9l5.5-4.5z" fill-rule="evenodd"/></svg>
      </li>
      <li>www.harborviewest.com
        <svg viewBox="0 0 16 16" aria-label="Website"><circle cx="8" cy="8" r="7"/><path d="M5 5h3v3H5zM9 9h3v2H9z" fill="var(--paper)"/></svg>
      </li>
    </ul>
  </section>
</body>
</html>
```